Business Card Design Project

Business Card
We are rebranding with a new logo
Industry/Entity Type
Business
Contact Information for Business Card
Dennis Morvale +61 487215963 dennis@quorv.com.au P.O. Box 872 Fernlow QLD 4309
Requirements
Must have
- Logo

```html
<!DOCTYPE html>
<html lang="en">
<head>
<meta charset="utf-8">
<title>Quorv International – Business Card</title>
<link href="https://fonts.googleapis.com/css2?family=Roboto:wght@400;500&family=Roboto+Condensed:wght@700&display=swap" rel="stylesheet">
<style>
  :root {
    --backdrop: #262626;
    --card: #f4f4f4;
    --brand-blue: #0a6e9e;
    --blue-light: #10a8df;
    --blue-dark: #03506f;
    --accent-orange: #f28a1e;
    --text-light: #ffffff;
  }
  html, body {
    margin: 0;
    width: 1200px;
    height: 960px;
    overflow: hidden;
    background: var(--backdrop);
  }
  .business-card {
    position: absolute;
    left: 314px;
    top: 294px;
    width: 600px;
    height: 342px;
    border-radius: 22px;
    background: var(--card);
    overflow: hidden;
  }
  .card-swoosh {
    position: absolute;
    inset: 0;
  }
  .brand-name {
    position: absolute;
    left: 30px;
    top: 108px;
    margin: 0;
    font-family: "Roboto", sans-serif;
    font-weight: 500;
    color: var(--brand-blue);
    line-height: 1;
  }
  .brand-name .brand-word {
    display: block;
    font-size: 58px;
    letter-spacing: 1px;
  }
  .brand-name .brand-sub {
    display: block;
    margin-top: 16px;
    font-size: 18px;
    letter-spacing: 3.6px;
  }
  .contact-block {
    position: absolute;
    right: 28px;
    top: 172px;
    text-align: right;
    color: var(--text-light);
    font-family: "Roboto", sans-serif;
    font-size: 14px;
  }
  .holder-name {
    margin: 0 0 18px;
    font-family: "Roboto Condensed", sans-serif;
    font-weight: 700;
    font-size: 21px;
    letter-spacing: 0.2px;
  }
  .postal-address {
    margin: 0 0 8px;
    font-style: normal;
    line-height: 18px;
  }
  .contact-list {
    list-style: none;
    margin: 0;
    padding: 0;
  }
  .contact-list li {
    display: flex;
    justify-content: flex-end;
    align-items: center;
    height: 19px;
    gap: 9px;
  }
  .contact-icon {
    width: 13px;
    height: 13px;
    fill: var(--text-light);
  }
</style>
</head>
<body>
  <div class="business-card">
    <svg class="card-swoosh" width="600" height="342" viewBox="0 0 600 342" aria-hidden="true">
      <defs>
        <radialGradient id="panelGlow" cx="400" cy="220" r="260" gradientUnits="userSpaceOnUse">
          <stop offset="0" stop-color="var(--blue-light)"/>
          <stop offset="1" stop-color="var(--blue-dark)"/>
        </radialGradient>
      </defs>
      <path d="M600,80 C400,104 262,160 202,342 L600,342 Z" fill="var(--accent-orange)"/>
      <path d="M600,84 C420,112 286,168 218,342 L600,342 Z" fill="url(#panelGlow)"/>
    </svg>

    <h1 class="brand-name">
      <span class="brand-word">Quorv</span>
      <span class="brand-sub">INTERNATIONAL</span>
    </h1>

    <div class="contact-block">
      <p class="holder-name">DENNIS MORVALE</p>
      <address class="postal-address">P.O. Box 872<br>Fernlow QLD 4309</address>
      <ul class="contact-list">
        <li>+61 487215963
          <svg class="contact-icon" viewBox="0 0 24 24"><path d="M6.6 10.8c1.4 2.8 3.8 5.1 6.6 6.6l2.2-2.2c.3-.3.7-.4 1-.2 1.1.4 2.3.6 3.6.6.6 0 1 .4 1 1V20c0 .6-.4 1-1 1C10.6 21 3 13.4 3 4c0-.6.4-1 1-1h3.5c.6 0 1 .4 1 1 0 1.3.2 2.5.6 3.6.1.3 0 .7-.2 1z"/></svg>
        </li>
        <li>dennis@quorv.com.au
          <svg class="contact-icon" viewBox="0 0 24 24"><path d="M2 5h20v14H2z M3 6l9 7 9-7" fill="none"/><path d="M2 5h20v2l-10 7L2 7z M2 9l10 7 10-7v10H2z"/></svg>
        </li>
        <li>www.quorv.com.au
          <svg class="contact-icon" viewBox="0 0 24 24"><circle cx="12" cy="12" r="10"/><path d="M8 6c2 1 1 3 3 4s0 3 2 4-1 4 1 5M15 5c-1 2 1 3 3 3" stroke="var(--blue-dark)" stroke-width="2" fill="none"/></svg>
        </li>
      </ul>
    </div>
  </div>
</body>
</html>
```